Business Card Design Project

Actor, Producer, Vocal Coach, Choral Director, Song WriterPhone: (215) 555-0142 Fax: (215) 856-3933Email: waltierblocker@gmail.comFacebook: facebook.com/waltier.blockerTwitter: @thedf482

Industry/Entity Type

Business

Contact Information for Business Card

Business Cards that include my picture

Colors

Designer to choose colors to be used in the design.

```html
<!DOCTYPE html>
<html lang="en">
<head>
<meta charset="utf-8">
<title>Dorian Fellsmore — Business Card</title>
<link rel="stylesheet" href="https://fonts.googleapis.com/css2?family=Cinzel:wght@400;700&family=Open+Sans:wght@400;600&display=swap">
<style>
  :root {
    --page-bg: #e9e6e1;
    --card-black: #131313;
    --card-white: #ffffff;
    --accent-red: #c3161c;
    --ink: #1a1a1a;
    --swoosh-grey: #c9c9c9;
    --photo-light: #eceae6;
    --photo-mid: #8a6f5a;
  }
  * { margin: 0; padding: 0; box-sizing: border-box; }
  html, body { width: 1200px; height: 900px; overflow: hidden; }
  body {
    background: var(--page-bg);
    display: flex;
    flex-direction: column;
    align-items: center;
    justify-content: center;
    gap: 56px;
    font-family: "Open Sans", sans-serif;
  }
  .card {
    position: relative;
    width: 620px;
    height: 354px;
    overflow: hidden;
    box-shadow: 0 6px 18px rgba(0,0,0,0.18);
  }
  /* Back side */
  .card--back {
    background: var(--card-black);
    display: flex;
    align-items: center;
    justify-content: center;
  }
  .back-name {
    font-family: "Cinzel", serif;
    font-weight: 400;
    font-size: 34px;
    letter-spacing: 0.16em;
    color: var(--accent-red);
  }
  /* Front side */
  .card--front { background: var(--card-white); color: var(--ink); }
  .front-swoosh { position: absolute; inset: 0; }
  .front-photo {
    position: absolute;
    left: 418px;
    top: 14px;
    width: 180px;
    height: 190px;
    background: linear-gradient(180deg, var(--photo-light) 0%, #d7d1ca 45%, var(--photo-mid) 100%);
  }
  .identity { position: absolute; left: 44px; top: 62px; }
  .front-name {
    font-family: "Cinzel", serif;
    font-weight: 700;
    font-size: 22px;
    letter-spacing: 0.03em;
    line-height: 1;
  }
  .roles { margin-top: 6px; font-size: 12.5px; line-height: 1.35; width: 230px; }
  .contacts { position: absolute; left: 44px; top: 158px; list-style: none; }
  .contacts li {
    display: flex;
    align-items: center;
    gap: 7px;
    font-size: 13px;
    line-height: 19px;
  }
  .contacts svg { width: 12px; height: 12px; fill: var(--ink); }
  .socials { position: absolute; left: 44px; top: 228px; list-style: none; }
  .socials li {
    display: flex;
    align-items: center;
    gap: 8px;
    font-size: 14px;
    margin-bottom: 6px;
  }
  .social-square { width: 22px; height: 22px; background: var(--ink); }
</style>
</head>
<body>
  <section class="card card--back" aria-label="Card back">
    <h1 class="back-name">Dorian Fellsmore</h1>
  </section>

  <section class="card card--front" aria-label="Card front">
    <svg class="front-swoosh" viewBox="0 0 620 354" preserveAspectRatio="none" aria-hidden="true">
      <path d="M0,288 C180,332 420,300 620,162 L620,354 L0,354 Z" fill="var(--swoosh-grey)"/>
      <path d="M0,300 C180,340 420,312 620,176 L620,354 L0,354 Z" fill="var(--card-white)"/>
      <path d="M0,312 C190,346 430,322 620,188 L620,354 L0,354 Z" fill="var(--card-black)"/>
    </svg>

    <div class="front-photo" role="img" aria-label="Portrait photo of Dorian Fellsmore in white shirt and pink tie"></div>

    <div class="identity">
      <h2 class="front-name">Dorian Fellsmore</h2>
      <p class="roles">Actor, Producer, Vocal Coach, Choral Director, Song Writer</p>
    </div>

    <ul class="contacts">
      <li>
        <svg viewBox="0 0 24 24" aria-hidden="true"><path d="M6.6 10.8a15 15 0 0 0 6.6 6.6l2.2-2.2a1 1 0 0 1 1-.25 11.4 11.4 0 0 0 3.6.57 1 1 0 0 1 1 1V20a1 1 0 0 1-1 1A17 17 0 0 1 3 4a1 1 0 0 1 1-1h3.5a1 1 0 0 1 1 1c0 1.25.2 2.45.57 3.57a1 1 0 0 1-.25 1z"/></svg>
        (215) 555-0142
      </li>
      <li>
        <svg viewBox="0 0 24 24" aria-hidden="true"><path d="M7 2h8v6H7zM3 9h18v12H3zm4 3v2h4v-2zm0 4v2h4v-2zm7-4v2h4v-2zm0 4v2h4v-2z"/></svg>
        (215) 555-0187
      </li>
      <li>
        <svg viewBox="0 0 24 24" aria-hidden="true"><path d="M2 5h20v14H2zm2 2v.5l8 5.5 8-5.5V7l-8 5.5z"/></svg>
        dorianfellsmore@postlane.net
      </li>
    </ul>

    <ul class="socials">
      <li><span class="social-square" aria-hidden="true"></span>@thedf482</li>
      <li><span class="social-square" aria-hidden="true"></span>socialpage.net/dorian.fellsmore</li>
    </ul>
  </section>
</body>
</html>
```